Super elegant, crisp & clean Business card design required

We recently upgraded our branding - which is on our website - talvendoraphoto.com

I would like a simple, yet elegant, clean business card design please.

The font of my logo is Cinzel - and because of the natural colour - it's best to have this on a black background.

I would like to have the back of the business card - with simply my logo.

PLEASE DO NOT SUBMIT A COMPLICATED / UNCLEAN DESIGN

Industry/Entity Type

Business

Contact Information for Business Card

Talven Doroshko Photography

Font styles to use
Other font styles liked:
• Cinzel

Requirements
Must have
• A backpage with nothing but my logo
• Simple design - stands out
Should not have
• Colour that dont align with my logo
• Over complicated '/ non symmetrical design

```html
<!DOCTYPE html>
<html lang="en">
<head>
<meta charset="utf-8">
<title>Talven Doroshko Photography – Business Card</title>
<link href="https://fonts.googleapis.com/css2?family=Cinzel:wght@400;700&display=swap" rel="stylesheet">
<style>
  :root {
    --backdrop: #2b2b2b;
    --card: #050505;
    --ink: #f2f2f2;
    --ink-soft: #cfcfcf;
    --rule: #e6e6e6;
  }
  * { box-sizing: border-box; margin: 0; padding: 0; }
  html, body {
    width: 1200px;
    height: 900px;
    overflow: hidden;
    background: var(--backdrop);
  }
  .stage {
    position: relative;
    width: 1200px;
    height: 900px;
    display: flex;
    flex-direction: column;
    align-items: center;
    justify-content: center;
    gap: 52px;
  }
  .card {
    position: relative;
    width: 620px;
    height: 354px;
    background: var(--card);
    border-radius: 22px;
    color: var(--ink);
    font-family: "Cinzel", serif;
  }

  /* Back side: brand name only */
  .card-back {
    display: flex;
    align-items: center;
    justify-content: center;
  }
  .brand-mark {
    text-align: center;
    font-weight: 400;
    color: var(--ink);
    line-height: 1.25;
  }
  .brand-mark .brand-name { font-size: 34px; letter-spacing: 1px; }
  .brand-mark .brand-trade { font-size: 16px; letter-spacing: 6px; }

  /* Front side */
  .brand-block {
    position: absolute;
    left: 40px;
    top: 62px;
    font-weight: 400;
    color: var(--ink);
    text-align: center;
    line-height: 1.3;
  }
  .brand-block .brand-name { font-size: 17px; letter-spacing: 0.5px; }
  .brand-block .brand-trade { font-size: 10px; letter-spacing: 5px; }

  .owner {
    position: absolute;
    right: 34px;
    top: 150px;
    text-align: right;
  }
  .owner-name {
    font-size: 21px;
    font-weight: 700;
    letter-spacing: 0.5px;
  }
  .owner-role {
    font-size: 12px;
    color: var(--ink-soft);
    letter-spacing: 0.5px;
    margin-top: 2px;
  }
  .divider {
    position: absolute;
    left: 26px;
    right: 34px;
    top: 200px;
    height: 2px;
    background: var(--rule);
  }
  .contact-list {
    position: absolute;
    left: 30px;
    top: 228px;
    list-style: none;
  }
  .contact-item {
    display: flex;
    align-items: center;
    gap: 12px;
    font-size: 14px;
    letter-spacing: 0.5px;
    color: var(--ink);
    height: 28px;
  }
  .contact-icon {
    width: 12px;
    height: 12px;
    fill: var(--ink-soft);
    stroke: var(--ink-soft);
  }
</style>
</head>
<body>
<main class="stage">

  <section class="card card-back" aria-label="Card back">
    <div class="brand-mark">
      <div class="brand-name">Talven Doroshko</div>
      <div class="brand-trade">Photography</div>
    </div>
  </section>

  <section class="card card-front" aria-label="Card front">
    <div class="brand-block">
      <div class="brand-name">Talven Doroshko</div>
      <div class="brand-trade">Photography</div>
    </div>

    <div class="owner">
      <div class="owner-name">Talven Doroshko</div>
      <div class="owner-role">Photography</div>
    </div>

    <div class="divider"></div>

    <ul class="contact-list">
      <li class="contact-item">
        <svg class="contact-icon" viewBox="0 0 12 12" aria-hidden="true">
          <path stroke="none" d="M2.4 0.8l2 2.1-1 1.3c0.7 1.5 1.8 2.6 3.3 3.3l1.3-1 2.1 2-1.2 1.9C5.2 10.3 1.7 6.8 0.6 2z"/>
        </svg>
        <span>+330 2460-5193</span>
      </li>
      <li class="contact-item">
        <svg class="contact-icon" viewBox="0 0 12 12" aria-hidden="true">
          <rect x="0.8" y="2.3" width="10.4" height="7.4" fill="none" stroke-width="1.2"/>
          <path d="M0.8 2.6L6 6.6l5.2-4" fill="none" stroke-width="1.2"/>
        </svg>
        <span>info@talvendoraphoto.com</span>
      </li>
      <li class="contact-item">
        <svg class="contact-icon" viewBox="0 0 12 12" aria-hidden="true">
          <circle cx="6" cy="6" r="5.2" fill="none" stroke-width="1.1"/>
          <ellipse cx="6" cy="6" rx="2.3" ry="5.2" fill="none" stroke-width="1"/>
          <path d="M0.8 6h10.4" fill="none" stroke-width="1"/>
        </svg>
        <span>www.talvendoraphoto.com</span>
      </li>
    </ul>
  </section>

</main>
</body>
</html>
```